Halvor Grading and Septic needs a flyer to submit to contractors to offer our services

I need a sleek profession one page full color high gloss document showcasing our services to give to Mobile Home Companies and contractors that need our services.

Target Market(s)

Home Builders. Mobile Home Salesmen. People Building new homes.

Industry/Entity Type

Construction

Font styles to use
Serif
Sans Serif

Requirements
Must have
• Phone Number. Email address. Logo. Services offered: Mobile Home Pads, Meter Pole Placement and Connection, Waterline Connection, On Site Septic System Installs
Should not have
• Jokes, Nothing trying to be cute

```html
<!DOCTYPE html>
<html lang="en">
<head>
<meta charset="utf-8">
<title>Halvor Grading and Septic – Services Flyer</title>
<link rel="stylesheet" href="https://fonts.googleapis.com/css2?family=Oswald:wght@400;500;600;700&display=swap">
<style>
  :root {
    --brand-blue: #17508c;
    --deep-blue: #24487e;
    --brand-red: #c8070f;
    --earth-dark: #1e3a44;
    --earth-mid: #2c4d57;
    --sky-light: #eceef0;
    --white: #ffffff;
  }
  * { margin: 0; padding: 0; box-sizing: border-box; }
  html, body { width: 849px; height: 1200px; overflow: hidden; }
  body { font-family: "Oswald", sans-serif; background: var(--earth-dark); }

  .flyer { position: relative; width: 849px; height: 1200px; overflow: hidden; }

  .backdrop-earth {
    position: absolute; inset: 0;
    background: radial-gradient(ellipse at 50% 60%, var(--earth-mid), var(--earth-dark) 75%);
  }
  .backdrop-site {
    position: absolute; inset: 0;
    background: linear-gradient(180deg, #e4e7ea 0%, var(--sky-light) 60%, #f3f4f5 100%);
    clip-path: polygon(0 0, 849px 0, 849px 160px, 530px 680px, 425px 640px, 320px 680px, 0 160px);
  }

  .brand {
    position: absolute; top: 62px; left: 0; width: 849px;
    display: flex; flex-direction: column; align-items: center; gap: 4px;
  }
  .brand-name {
    color: var(--brand-blue); font-weight: 700; font-size: 40px;
    letter-spacing: 1px; line-height: 1; text-transform: uppercase; text-align: center;
  }
  .brand-name-sub { font-size: 30px; }

  .headline {
    position: absolute; top: 220px; left: 0; width: 849px; text-align: center;
    color: var(--brand-blue); font-weight: 500; font-size: 52px; line-height: 72px;
    text-transform: uppercase; letter-spacing: -1px;
  }

  .diamond {
    position: absolute; transform: rotate(45deg);
    border: 13px solid var(--white); border-radius: 46px; overflow: hidden;
  }
  .diamond-photo { width: 274px; height: 274px; top: 408px; }
  .diamond-photo.left { left: 65px; background: linear-gradient(135deg, #3f7fd6 0%, #b9bcbd 45%, #c5733d 75%, #6f9a45 100%); }
  .diamond-photo.right { left: 510px; background: linear-gradient(135deg, #4f7a3b 0%, #d6a35a 40%, #c99467 70%, #d8d4cc 100%); }

  .diamond-services {
    width: 365px; height: 365px; left: 242px; top: 622px;
    border-width: 14px; border-radius: 60px;
    background: linear-gradient(135deg, var(--brand-red) 0%, #7a2244 50%, var(--deep-blue) 100%);
  }

  .services {
    position: absolute; top: 692px; left: 0; width: 849px; text-align: center; color: var(--white);
  }
  .services-title { font-weight: 600; font-size: 36px; line-height: 50px; margin-bottom: 2px; }
  .services-list { list-style: none; font-weight: 400; font-size: 24px; line-height: 34px; }

  .contact-band {
    position: absolute; left: 0; bottom: 0; width: 849px; height: 112px;
    background: linear-gradient(90deg, var(--deep-blue) 0%, #6a2a4a 50%, var(--brand-red) 100%);
    display: flex; align-items: center; padding: 0 0 0 36px; color: var(--white);
  }
  .contact-item { display: flex; align-items: center; }
  .contact-icon { flex: none; display: block; }
  .contact-phone { font-weight: 600; font-size: 48px; margin-left: 12px; line-height: 1; }
  .contact-email-item { margin-left: 52px; }
  .contact-email { font-weight: 500; font-size: 25px; margin-left: 12px; }
</style>
</head>
<body>
<main class="flyer">
  <div class="backdrop-earth" role="img" aria-label="Photo of excavated earth and soil"></div>
  <div class="backdrop-site" role="img" aria-label="Faded photo of an excavator at a mobile home site"></div>

  <header class="brand">
    <span class="brand-name">Halvor</span>
    <span class="brand-name brand-name-sub">Grading &amp; Septic</span>
  </header>

  <h1 class="headline">Your trusted partner for<br>precision excavation</h1>

  <div class="diamond diamond-photo left" role="img" aria-label="Photo of a concrete septic tank being lifted into place by a crane"></div>
  <div class="diamond diamond-photo right" role="img" aria-label="Photo of an excavator beside an installed septic tank with green lids"></div>
  <div class="diamond diamond-services"></div>

  <section class="services">
    <h2 class="services-title">OUR SERVICES</h2>
    <ul class="services-list">
      <li>Mobile Home Pads,</li>
      <li>Meter Pole Placement and Connection,</li>
      <li>Waterline Connection,</li>
      <li>On Site Septic</li>
      <li>System Installs</li>
    </ul>
  </section>

  <footer class="contact-band">
    <div class="contact-item">
      <svg class="contact-icon" width="52" height="52" viewBox="0 0 52 52" aria-hidden="true">
        <circle cx="26" cy="26" r="26" fill="#ffffff"/>
        <path d="M18 13c1.5-1 3-.6 3.8.8l2.4 4.3c.7 1.3.3 2.6-.8 3.4l-1.8 1.3c.9 2.8 3.2 5.6 6 7.2l1.5-1.6c1-1 2.4-1.2 3.5-.4l4 2.8c1.3.9 1.5 2.5.4 3.8l-1.7 2c-1.4 1.6-3.8 2-6 1-6.6-3-11.6-8.7-13.7-15.6-.7-2.3 0-4.6 1.7-6z" fill="#24487e"/>
      </svg>
      <span class="contact-phone">(555) 214-0738</span>
    </div>
    <div class="contact-item contact-email-item">
      <svg class="contact-icon" width="38" height="38" viewBox="0 0 38 38" aria-hidden="true">
        <circle cx="19" cy="19" r="19" fill="#ffffff"/>
        <rect x="10" y="12.5" width="18" height="13" fill="none" stroke="#6a2a4a" stroke-width="1.8"/>
        <path d="M10 12.5l9 7.5 9-7.5M10 25.5l6.5-6M28 25.5l-6.5-6" fill="none" stroke="#6a2a4a" stroke-width="1.6"/>
      </svg>
      <span class="contact-email">erik@halvorgradingseptic.com</span>
    </div>
  </footer>
</main>
</body>
</html>
```